Business Card Design

We need a business card designed for our new company. Prefer a black card with white logo & writing.

Contact Information for Business Card

Ted Galloway, address: 7-4812 Fernhollow Road, Abbotsford, BC, V3K 8R2, Office Phone: 604-712-3390, Cell: 604-947-2164, Email: ted@resinworkshub.ca

Colors

Designer to choose only greyscale colors for use in the design.

```html
<!DOCTYPE html>
<html lang="en">
<head>
<meta charset="utf-8">
<title>Resin Works Hub – Business Card</title>
<link href="https://fonts.googleapis.com/css2?family=Poppins:wght@300;400;500;700;800&display=swap" rel="stylesheet">
<style>
  :root {
    --stage: #222222;
    --card: #1f1f1f;
    --ink: #ffffff;
    --ink-soft: #d9d9d9;
    --band-text: #1a1a1a;
    --rule: #8a8a8a;
  }
  * { margin: 0; padding: 0; box-sizing: border-box; }
  html, body {
    width: 1200px; height: 780px; overflow: hidden;
    background: var(--stage);
    font-family: "Poppins", sans-serif;
    color: var(--ink);
  }
  .stage {
    width: 1200px; height: 780px;
    display: flex; align-items: center; justify-content: center; gap: 40px;
  }
  .card {
    position: relative;
    width: 540px; height: 309px;
    background: var(--card);
    box-shadow: 0 18px 40px rgba(0,0,0,.45);
    overflow: hidden;
  }

  /* Front: contact side */
  .card-front .brand {
    position: absolute; left: 28px; top: 82px; width: 220px;
    display: flex; align-items: center; gap: 12px;
  }
  .brand-dot {
    flex: none; width: 30px; height: 30px; border-radius: 50%;
    background: var(--ink);
  }
  .brand-name {
    font-weight: 700; font-size: 25px; line-height: 1.05;
    text-transform: uppercase; letter-spacing: .5px;
  }
  .divider {
    position: absolute; left: 268px; top: 28px; width: 1px; height: 168px;
    background: linear-gradient(to bottom, transparent, var(--rule) 40%, var(--rule) 60%, transparent);
  }
  .identity { position: absolute; left: 296px; top: 32px; }
  .person-name { font-size: 29px; font-weight: 300; line-height: 1.1; }
  .person-name strong { font-weight: 800; }
  .person-role { font-size: 12.5px; font-weight: 300; color: var(--ink-soft); margin-top: 2px; }
  .contact-list { list-style: none; margin-top: 14px; }
  .contact-list li {
    display: flex; align-items: center; gap: 9px;
    font-size: 13px; font-weight: 300; line-height: 21px; color: var(--ink-soft);
  }
  .contact-list svg { width: 13px; height: 13px; flex: none; }

  .address-band {
    position: absolute; left: 0; bottom: 26px;
    width: 455px; height: 34px;
    background: var(--ink);
    clip-path: polygon(0 0, 100% 0, 96% 50%, 100% 100%, 0 100%);
    display: flex; align-items: center; padding-left: 26px;
    color: var(--band-text); font-size: 14.5px; font-weight: 500; letter-spacing: .2px;
  }

  /* Back: brand side */
  .card-back { display: flex; align-items: center; justify-content: center; }
  .card-back .brand { display: flex; align-items: center; gap: 18px; }
  .card-back .brand-dot { width: 46px; height: 46px; }
  .card-back .brand-name { font-size: 40px; }
</style>
</head>
<body>
<main class="stage">
  <section class="card card-front" aria-label="Business card, contact side">
    <div class="brand">
      <span class="brand-dot"></span>
      <span class="brand-name">Resin Works Hub</span>
    </div>
    <div class="divider"></div>
    <div class="identity">
      <h1 class="person-name"><strong>Ted</strong> Galloway</h1>
      <p class="person-role">Founder &amp; CEO</p>
      <ul class="contact-list">
        <li>
          <svg viewBox="0 0 16 16" fill="#fff" aria-hidden="true"><path d="M3.6 1.2l2.3 2.6-1.3 1.9c.9 2 2.5 3.6 4.6 4.6l1.9-1.3 2.6 2.3-1.4 2.4C7 13.2 2.8 9 1.3 2.6z"/></svg>
          604-712-3390
        </li>
        <li>
          <svg viewBox="0 0 16 16" fill="none" stroke="#fff" stroke-width="1.5" aria-hidden="true"><rect x="4" y="1" width="8" height="14" rx="1.5"/><line x1="7" y1="12.5" x2="9" y2="12.5"/></svg>
          604-947-2164
        </li>
        <li>
          <svg viewBox="0 0 16 16" fill="none" stroke="#fff" stroke-width="1.3" aria-hidden="true"><circle cx="8" cy="8" r="6.5"/><ellipse cx="8" cy="8" rx="2.8" ry="6.5"/><line x1="1.5" y1="8" x2="14.5" y2="8"/></svg>
          www.resinworkshub.ca
        </li>
        <li>
          <svg viewBox="0 0 16 16" fill="none" stroke="#fff" stroke-width="1.4" aria-hidden="true"><rect x="1" y="3" width="14" height="10" rx="1"/><path d="M1.5 3.5L8 9l6.5-5.5"/></svg>
          ted@resinworkshub.ca
        </li>
      </ul>
    </div>
    <div class="address-band">7-4812 Fernhollow Road, Abbotsford, BC, V3K 8R2.</div>
  </section>

  <section class="card card-back" aria-label="Business card, brand side">
    <div class="brand">
      <span class="brand-dot"></span>
      <span class="brand-name">Resin Works Hub</span>
    </div>
  </section>
</main>
</body>
</html>
```